Simple proffessional BC

I have a logo which I will attach below.
I would like the logo on the front of the card with these details in point form below:
Pre and Post Natal Yoga: Pregnancy Workshops: Hypnobirthing Courses
On the back of the card my details:
Marla Pennick
Facebook page- stretchbelliesbayridgefield
Mobile- 0491 352 718

I like the idea of the card being simple, possibly just the above on a plain coloured (eggshell?) card, a card that is textured.
I am open to suggestion if it appeals!
Thank you and good luck!

Target Market(s)

Pregnant women, 20's-40's

Requirements
Must have
• Simple, compliment logo.
Make logo the feature.
Should not have

• .

```html
<!DOCTYPE html>
<html lang="en">
<head>
<meta charset="utf-8">
<title>Stretch Bellies – Business Card</title>
<link rel="stylesheet" href="https://fonts.googleapis.com/css2?family=Open+Sans:wght@400;600;700&display=swap">
<style>
  :root {
    --backdrop: #e4e2df;
    --card: #fbfbfa;
    --card-shade: #efefee;
    --berry: #8e2a2c;
    --saffron: #eda63a;
    --ink: #4a4444;
  }
  * { box-sizing: border-box; margin: 0; padding: 0; }
  html, body { width: 1200px; height: 800px; overflow: hidden; }
  body {
    background: var(--backdrop);
    font-family: "Open Sans", sans-serif;
    position: relative;
  }
  .card {
    position: absolute;
    background: radial-gradient(circle at 55% 45%, var(--card) 40%, var(--card-shade) 100%);
    box-shadow: 0 6px 18px rgba(0,0,0,.18);
    overflow: hidden;
  }
  .card--front { left: 110px; top: 240px; width: 560px; height: 320px; }
  .card--back  { left: 730px; top: 120px; width: 320px; height: 560px; }

  .front__swoosh { position: absolute; inset: 0; width: 100%; height: 100%; }

  .brand { position: absolute; left: 44px; top: 40px; width: 250px; text-align: center; }
  .brand__mark {
    display: block; width: 76px; height: 76px; border-radius: 50%;
    background: var(--saffron); margin: 0 auto 10px;
  }
  .brand__name { font-size: 34px; font-weight: 400; color: var(--berry); letter-spacing: .5px; }

  .contact {
    position: absolute; right: 34px; top: 54px; text-align: right;
    color: var(--ink); font-size: 12px; line-height: 1.55;
  }
  .contact__name { font-size: 17px; font-weight: 700; color: var(--berry); margin-bottom: 22px; }
  .services { list-style: none; margin-bottom: 12px; }
  .services li::after { content: ""; display: inline-block; width: 5px; height: 5px; border-radius: 50%; background: var(--berry); margin: 0 3px 2px 11px; }
  .contact__row { display: flex; justify-content: flex-end; align-items: center; gap: 8px; }
  .contact__row svg { width: 11px; height: 11px; fill: var(--berry); flex: none; }

  .back__mark {
    position: absolute; left: 50%; top: 50%; transform: translate(-62%, -55%);
    width: 140px; height: 140px; border-radius: 50%; background: var(--saffron);
    display: flex; align-items: center; justify-content: center; text-align: center;
  }
  .back__name { color: var(--berry); font-size: 17px; font-weight: 600; line-height: 1.2; }
  .back__tab {
    position: absolute; right: 0; top: 300px; width: 46px; height: 220px;
    background: var(--saffron); border-radius: 24px 0 0 24px;
    display: flex; align-items: center; justify-content: center;
  }
  .back__web {
    transform: rotate(-90deg); white-space: nowrap; color: #fff;
    font-size: 11px; letter-spacing: 1.5px;
  }
</style>
</head>
<body>
  <section class="card card--front">
    <svg class="front__swoosh" viewBox="0 0 560 320" preserveAspectRatio="none" aria-hidden="true">
      <path d="M0,182 C170,210 340,250 470,320 L458,320 C330,258 160,222 0,196 Z" fill="var(--saffron)"/>
      <path d="M0,204 C160,232 320,270 440,320 L0,320 Z" fill="var(--berry)"/>
    </svg>

    <div class="brand">
      <span class="brand__mark"></span>
      <p class="brand__name">Stretch Bellies</p>
    </div>

    <div class="contact">
      <p class="contact__name">Marla Pennick</p>
      <ul class="services">
        <li>Pre &amp; Post Natal Yoga</li>
        <li>Pregnancy Workshops</li>
        <li>Hypnobirthing Courses</li>
      </ul>
      <div class="contact__row"><span>Mobile: 0491 352 718</span>
        <svg viewBox="0 0 12 12"><rect x="3" y="0.5" width="6" height="11" rx="1"/></svg></div>
      <div class="contact__row"><span>Facebook: stretchbelliesbayridgefield</span>
        <svg viewBox="0 0 12 12"><rect x="1" y="1" width="10" height="10" rx="1.5"/></svg></div>
    </div>
  </section>

  <section class="card card--back">
    <div class="back__mark"><p class="back__name">Stretch<br>Bellies</p></div>
    <div class="back__tab"><p class="back__web">www.stretchbellies.com</p></div>
  </section>
</body>
</html>
```